Magnetic Business Card Design. One sided

Not happy yet with a design yet currently winning so far are the designs 5162585 5135573 5132280

Logo
unmatched Quality through traditional friendly service" sound like a good line. Blockages, Hot water units & all plumbing services.
7days,
free quote: 0451 276 314
Maybe put on it: Qualified, Licensed
www.brightvaleplumbing.com.au

Make word as big so it is clearly able to be read

BrightVale Plumbing PTY LTD, target market is the middle aged mostly woman professional that owns a house and would rather pay a professional to do the job rather then a handyman.
We are a plumbing company based in Melbourne small and family owned with a focus on service to our customers.

I am after a design that is clean, professional and appealing to the eye which fits with the visual appearance of my web site and logo.

Our most profitable jobs are blockages and hot water units. however we do all types of plumbing. Maybe a point to make on the cards not sure tho.

I have included our previous magnet that i had designed with a printa nova template. if you can improve what we say to get new customers or totally change what is on the magnet. that would be fantastic.

I will also include other marketing material i have previously used

"unmatched Quality Through traditional friendly service" Could be a good catch line

These magnets are dropped into thousands of letter boxes and hopefully will find there way onto new clients fridges. Fridges in million dollar plus houses.

I really look forward to seeing your design. Thank you

Industry/Entity Type

Marketing

Contact Information for Business Card

Number: 0451 276 314
Web site: www.Brightvaleplumbing.com.au

```html
<!DOCTYPE html>
<html lang="en">
<head>
<meta charset="utf-8">
<title>BrightVale Plumbing – Magnet Card</title>
<link href="https://fonts.googleapis.com/css2?family=Open+Sans:wght@400;600;700;800&family=Anton&family=Roboto+Condensed:wght@400;700&display=swap" rel="stylesheet">
<style>
  :root {
    --navy: #15163f;
    --blue: #1f4f9f;
    --ink: #111111;
    --white: #ffffff;
    --bg-light: #f7f8fa;
    --bg-edge: #c9cdd3;
    --black: #000000;
  }
  * { margin: 0; padding: 0; box-sizing: border-box; }
  html, body { width: 1200px; height: 740px; overflow: hidden; }
  body { font-family: "Open Sans", sans-serif; color: var(--ink); }

  .card {
    position: relative;
    width: 1200px;
    height: 740px;
    overflow: hidden;
    background: radial-gradient(ellipse at 50% 45%, var(--bg-light) 0%, #e6e8eb 55%, var(--bg-edge) 100%);
  }

  .brand {
    position: absolute;
    left: 60px;
    top: 70px;
    width: 760px;
    color: var(--navy);
    font-family: "Open Sans", sans-serif;
    font-weight: 800;
    line-height: 1;
  }
  .brand-name { display: block; font-size: 120px; letter-spacing: -2px; }
  .brand-sub { display: block; font-size: 62px; letter-spacing: 14px; margin-top: 20px; padding-left: 150px; }

  .hours {
    position: absolute;
    left: 865px;
    top: 98px;
    width: 290px;
    text-align: center;
  }
  .hours-days {
    display: flex;
    align-items: center;
    justify-content: flex-end;
    gap: 8px;
    color: var(--blue);
    font-weight: 700;
    font-size: 48px;
    line-height: 60px;
  }
  .hours-days svg { width: 62px; height: 58px; }
  .hours-line {
    font-size: 48px;
    line-height: 58px;
    color: var(--ink);
    padding-left: 10px;
  }

  .heritage-band {
    position: absolute;
    left: 0;
    top: 333px;
    width: 1200px;
    height: 48px;
  }
  .heritage-band .pipe { position: absolute; top: 0; left: 0; width: 1200px; height: 48px; background: var(--navy); }
  .heritage-band .coupling {
    position: absolute;
    top: -4px;
    width: 12px;
    height: 56px;
    background: var(--blue);
    border-radius: 2px;
  }
  .heritage-band .label {
    position: absolute;
    left: 0; right: 0; top: 0;
    text-align: center;
    color: var(--white);
    font-weight: 600;
    font-size: 24px;
    letter-spacing: 4px;
    line-height: 48px;
  }

  .tagline {
    position: absolute;
    left: 0; right: 0; top: 392px;
    text-align: center;
    font-family: "Anton", sans-serif;
    font-size: 46px;
    line-height: 58px;
    color: var(--ink);
    letter-spacing: 0.3px;
  }
  .services {
    position: absolute;
    left: 0; right: 0; top: 458px;
    text-align: center;
    font-size: 40px;
    line-height: 56px;
    color: var(--ink);
  }

  .credentials {
    position: absolute;
    left: 92px;
    top: 535px;
    display: flex;
    align-items: center;
    gap: 18px;
  }
  .credentials svg { width: 54px; height: 80px; }
  .credentials .text {
    font-weight: 600;
    font-size: 25px;
    letter-spacing: 3px;
    line-height: 36px;
    color: var(--ink);
  }

  .quote-panel { position: absolute; left: 390px; top: 525px; width: 810px; height: 101px; }
  .quote-panel svg.shape { position: absolute; inset: 0; width: 810px; height: 101px; }
  .quote-panel .quote {
    position: absolute;
    left: 46px;
    top: 0;
    height: 101px;
    display: flex;
    align-items: center;
    gap: 12px;
    color: var(--white);
    font-family: "Roboto Condensed", sans-serif;
    white-space: nowrap;
  }
  .quote .lead { font-size: 64px; font-weight: 400; }
  .quote .phone-icon { width: 36px; height: 46px; margin-left: 4px; }
  .quote .number { font-size: 66px; font-weight: 700; letter-spacing: 1px; }

  .web-band {
    position: absolute;
    left: 0; top: 626px;
    width: 1200px; height: 114px;
    background: var(--black);
    color: var(--white);
    text-align: center;
    font-size: 62px;
    line-height: 108px;
  }
  .web-band strong { font-weight: 700; }
</style>
</head>
<body>
<main class="card">

  <h1 class="brand">
    <span class="brand-name">BrightVale</span>
    <span class="brand-sub">PLUMBING</span>
  </h1>

  <section class="hours">
    <div class="hours-days">
      <svg viewBox="0 0 62 58" aria-hidden="true">
        <rect x="2" y="26" width="30" height="20" rx="2" fill="#15163f"/>
        <path d="M32 32h10l6 7v7H32z" fill="#15163f"/>
        <circle cx="12" cy="49" r="5" fill="#15163f" stroke="#fff" stroke-width="2"/>
        <circle cx="40" cy="49" r="5" fill="#15163f" stroke="#fff" stroke-width="2"/>
        <circle cx="40" cy="18" r="16" fill="#fff" stroke="#15163f" stroke-width="3"/>
        <path d="M40 9v9l6 5" fill="none" stroke="#15163f" stroke-width="3" stroke-linecap="round"/>
      </svg>
      <span>7 DAYS</span>
    </div>
    <div class="hours-line">affordable</div>
    <div class="hours-line">&amp; reliable</div>
  </section>

  <div class="heritage-band">
    <div class="pipe"></div>
    <span class="coupling" style="left:46px"></span>
    <span class="coupling" style="left:62px"></span>
    <span class="coupling" style="left:1128px"></span>
    <span class="coupling" style="left:1144px"></span>
    <p class="label">FAMILY OWNED SINCE 1980</p>
  </div>

  <h2 class="tagline">UNMATCHED QUALITY THROUGH TRADITION FRIENDLY SERVICE</h2>
  <p class="services">Blockages, hot water units &amp; all plumbing services.</p>

  <div class="credentials">
    <svg viewBox="0 0 54 80" aria-hidden="true">
      <path d="M12 44 L6 76 L16 70 L22 78 L27 52 Z" fill="#111"/>
      <path d="M42 44 L48 76 L38 70 L32 78 L27 52 Z" fill="#111"/>
      <circle cx="27" cy="27" r="25" fill="#111"/>
      <circle cx="27" cy="27" r="17" fill="none" stroke="#fff" stroke-width="3"/>
    </svg>
    <div class="text">QUALIFIED<br>LICENSED</div>
  </div>

  <div class="quote-panel">
    <svg class="shape" viewBox="0 0 810 101" preserveAspectRatio="none" aria-hidden="true">
      <path d="M0 101 C22 40 42 2 100 2 L810 2 L810 101 Z" fill="#1f4f9f"/>
    </svg>
    <div class="quote">
      <span class="lead">Free Quote</span>
      <svg class="phone-icon" viewBox="0 0 24 30" aria-hidden="true">
        <path d="M5 2 L10 1 L12 9 L8 11 C9 16 11 20 14 23 L17 20 L22 25 L19 29 C10 28 2 16 5 2 Z" fill="#fff"/>
      </svg>
      <span class="number">0451 276 314</span>
    </div>
  </div>

  <footer class="web-band">www.<strong>BrightValePlumbing</strong>.com.au</footer>

</main>
</body>
</html>
```